creating a certificate for our flagship course

Hi,
We need a new certificate for our flagship course called Silver Harbour. We have been running this course for 25 years this year and want to get something special that represents that. We need our logos incorporated and we love to have a compass or Koru incorporated in the certificate. We like something different from your standard certificate, but not too crazy.

The text should say something along the lines of:
This certificate is awarded to ....
For successfully completing and contributing to the three day Silver Harbour programme.

signed:... date:...

to learn a bit more about this course and our company, please check our website. www.mellorquaid.co.nz

Thank you!

Target Market(s)

attendees who completed our 3 day programme.

Requirements
Must have
• Both our SH logo and our brand logo. a compass or a koru.
• a 25th year existence something on it.

```html
<!DOCTYPE html>
<html lang="en">
<head>
<meta charset="utf-8">
<title>Certificate of Completion – Silver Harbour</title>
<link rel="stylesheet" href="https://fonts.googleapis.com/css2?family=Open+Sans:wght@400;600;700;800&family=Pinyon+Script&display=swap">
<style>
  :root {
    --ink-navy: #3f3d52;
    --ink-black: #141414;
    --gold: #c99a35;
    --gold-light: #e2c170;
    --silver: #a8a8b2;
    --harbour-green: #8bc34a;
    --rule-grey: #9a9aa2;
    --paper: #ffffff;
  }
  * { box-sizing: border-box; margin: 0; padding: 0; }
  html, body { width: 928px; height: 1200px; overflow: hidden; background: var(--paper); }
  .certificate {
    position: relative;
    width: 928px;
    height: 1200px;
    background: var(--paper);
    font-family: "Open Sans", Arial, sans-serif;
    color: var(--ink-navy);
    overflow: hidden;
  }
  .guilloche-field {
    position: absolute;
    left: 0; top: 400px;
    width: 928px; height: 800px;
    background: radial-gradient(ellipse 460px 360px at 50% 48%, rgba(63,61,82,0.05), rgba(63,61,82,0.02) 60%, rgba(255,255,255,0) 100%);
  }
  .header-band { position: absolute; left: 0; top: 0; width: 928px; height: 300px; }
  .title {
    position: absolute; left: 0; width: 928px; text-align: center; color: #fff;
  }
  .title-main { top: 22px; font-size: 80px; font-weight: 700; letter-spacing: 9px; line-height: 1; }
  .title-sub { top: 120px; font-size: 34px; font-weight: 600; letter-spacing: 3px; line-height: 1; }
  .title-divider {
    position: absolute; top: 180px; left: 364px; width: 200px; height: 20px;
  }
  .anniversary {
    position: absolute; left: 280px; top: 290px;
    font-family: "Pinyon Script", cursive;
    font-size: 68px; color: var(--gold); white-space: nowrap;
    transform: rotate(-11deg); transform-origin: left center;
  }
  .course-mark {
    position: absolute; left: 152px; top: 474px;
    display: flex; align-items: center; gap: 36px;
  }
  .course-mark-square { width: 174px; height: 174px; background: var(--harbour-green); border-radius: 4px; }
  .course-mark-name { font-size: 62px; font-weight: 400; color: var(--ink-navy); letter-spacing: 0.5px; }
  .awarded-to {
    position: absolute; top: 714px; left: 0; width: 928px; text-align: center;
    font-size: 19px; font-weight: 700; letter-spacing: 0.3px;
  }
  .recipient {
    position: absolute; top: 768px; left: 0; width: 928px; text-align: center;
    font-size: 37px; font-weight: 800; color: var(--ink-black); letter-spacing: 0.5px;
  }
  .rule { position: absolute; height: 1.5px; background: var(--rule-grey); }
  .rule-long { top: 826px; left: 120px; width: 688px; }
  .rule-short { top: 836px; left: 288px; width: 354px; background: #c8c8cc; }
  .citation {
    position: absolute; top: 866px; left: 0; width: 928px; text-align: center;
    font-size: 19px; line-height: 29px; color: var(--ink-navy);
  }
  .brand-mark {
    position: absolute; left: 314px; top: 1012px;
    display: flex; align-items: center; gap: 16px;
  }
  .brand-mark-square { width: 64px; height: 64px; background: var(--ink-navy); }
  .brand-mark-name {
    font-size: 25px; font-weight: 600; color: var(--ink-navy);
    letter-spacing: 2px; line-height: 30px;
  }
  .sign-field {
    position: absolute; top: 1126px;
    display: flex; align-items: baseline; gap: 12px;
    font-size: 19px; font-weight: 700; color: var(--ink-navy);
  }
  .sign-field-line { display: inline-block; height: 2px; background: var(--ink-navy); }
  .sign-field-signature { left: 62px; }
  .sign-field-signature .sign-field-line { width: 188px; }
  .sign-field-date { left: 560px; }
  .sign-field-date .sign-field-line { width: 186px; }
</style>
</head>
<body>
<main class="certificate">
  <div class="guilloche-field" role="img" aria-label="Faint fine-line guilloche pattern behind the certificate body"></div>

  <svg class="header-band" viewBox="0 0 928 300" aria-hidden="true">
    <defs>
      <linearGradient id="goldSweep" x1="0" x2="1" y1="0" y2="0">
        <stop offset="0" stop-color="#b8862a"/>
        <stop offset="0.5" stop-color="#e6c56f"/>
        <stop offset="1" stop-color="#b8862a"/>
      </linearGradient>
      <linearGradient id="silverSweep" x1="0" x2="1" y1="0" y2="0">
        <stop offset="0" stop-color="#c9c9d1"/>
        <stop offset="0.5" stop-color="#8f8f9b"/>
        <stop offset="1" stop-color="#c4c4cc"/>
      </linearGradient>
    </defs>
    <path d="M0 0 H928 V100 C800 150 640 276 450 280 C290 284 170 190 0 124 Z" fill="url(#goldSweep)"/>
    <path d="M0 0 H928 V96 C800 140 640 262 450 266 C290 270 170 178 0 112 Z" fill="url(#silverSweep)"/>
    <path d="M0 0 H928 V92 C800 130 640 248 450 252 C300 256 170 160 0 96 Z" fill="var(--ink-navy)"/>
  </svg>

  <h1 class="title title-main">CERTIFICATE</h1>
  <p class="title title-sub">OF COMPLETION</p>
  <svg class="title-divider" viewBox="0 0 200 20" aria-hidden="true">
    <line x1="0" y1="10" x2="80" y2="10" stroke="#fff" stroke-width="2"/>
    <polygon points="100,1 102.6,7.4 109.5,7.9 104.2,12.3 105.9,19 100,15.3 94.1,19 95.8,12.3 90.5,7.9 97.4,7.4" fill="#fff"/>
    <line x1="120" y1="10" x2="200" y2="10" stroke="#fff" stroke-width="2"/>
  </svg>

  <p class="anniversary">25th year of existence</p>

  <div class="course-mark">
    <span class="course-mark-square" aria-hidden="true"></span>
    <span class="course-mark-name">Silver Harbour</span>
  </div>

  <p class="awarded-to">THIS CERTIFICATE IS AWARDED TO</p>
  <p class="recipient">AMELIA CARTER</p>
  <span class="rule rule-long"></span>
  <span class="rule rule-short"></span>
  <p class="citation">For successfully completing and contributing to the three day<br>Silver Harbour programme.</p>

  <div class="brand-mark">
    <span class="brand-mark-square" aria-hidden="true"></span>
    <span class="brand-mark-name">MELLOR QUAID<br>&amp; ASSOCIATES</span>
  </div>

  <p class="sign-field sign-field-signature">SIGNATURE <span class="sign-field-line"></span></p>
  <p class="sign-field sign-field-date">DATE <span class="sign-field-line"></span></p>
</main>
</body>
</html>
```